International game business needs app design

We are planning to release a new mobile game on iOS7 which requires a fresh, flat, reduced and functional design, fulfilling Norvex’s iOS7 design guidelines
.
The design shall be created for a dashboard, where players should be able to pick levels (icon + short description; 300+ levels), opponents (icon/photo/avatar image + short description; 5-100) and read/delete system/chat messages (icon, 2-3 actions (delete, accept/decline), text with up to 500 characters; 1-100 entries), Menu bar (settings, shop, leaderboards, achievements, and one or two more menu items) It must consider means to search/select levels and opponents. Would be nice to have an option to start playing immediately (with a random opponent on a random level)

Overall Style/Look: fresh, flat, functional, lot’s of free space, warm color scheme. If full screen images are being used it must be considered that there are user-generated photos or avatars which have to work with it in combination

Ideally the design is responsive and would work both on a smartphone and a tablet. Smartphone is top priority, tablet is optional.

The app will be a game for women predominantly, aged 25-35, with higher education and household net income, which should be reflected in color scheme, icons and navigation.

Some of us like flat design, so you might stick to that or impress all of us with something completely new!

The winner will have the chance to design all screens for the app and will have access to a much bigger budget.

UPDATE: A wireframe is attached - but you don't have to follow the depicted layout. Actually it would be highly appreciated if you could come up with something new. The only important thing is that all the listed components must appear somehow on the dashboard.

Target Market(s)

US, AU, NZ, GB, CA

Industry/Entity Type

Education

Colors

Designer to choose colors to be used in the design.

Requirements
Must have
• All the functional components described above.
Design must be in line with iOS7 design guidelines https://builders.norvexlabs.example/library/ios/documentation/UserExperience/Conceptual/MobileHIG/index.html
Nice to have
• We would like to have someone with the following attributes:
* minimum 5 ios design in your past at least 2 of them responsive – please provide links to the apps you created
* besides UI designer skills would be nice you to have UX skills

The most important factors for us are quality, creativity, speed, flexibility (“be able to take criticism into account”)
Should not have
• We don’t want a girly design so please don’t use too much pinks, flowers and such. The design should be acceptable by men too.

```html
<!DOCTYPE html>
<html lang="en">
<head>
<meta charset="utf-8">
<title>Game Dashboard</title>
<link rel="stylesheet" href="https://fonts.googleapis.com/css2?family=Open+Sans:wght@400;600;700&display=swap">
<style>
:root{
  --status-bg:#2a2a31;
  --nav-bg:#3e3b5e;
  --nav-icon:#a9a7bd;
  --page-bg:#f2f2f2;
  --pink:#f2466b;
  --navy:#35325c;
  --pill-grey:#c9c9c9;
  --icon-grey:#bcbcbc;
  --text-dark:#333333;
  --text-mid:#777777;
  --text-light:#9a9a9a;
  --white:#ffffff;
  --line:#dcdcdc;
  --ok:#8cc63f;
}
*{box-sizing:border-box;margin:0;padding:0}
html,body{width:710px;height:1200px;overflow:hidden}
body{font-family:"Open Sans",Arial,sans-serif;background:var(--page-bg);position:relative;color:var(--text-dark)}
.status-bar{position:absolute;left:0;top:0;width:710px;height:36px;background:var(--status-bg);color:var(--white);font-weight:600;font-size:21px;display:flex;align-items:center;padding:0 14px}
.status-bar .carrier{display:flex;align-items:center;gap:6px;width:220px}
.status-bar .time{flex:1;text-align:center}
.status-bar .battery{width:220px;display:flex;justify-content:flex-end;align-items:center;gap:8px}
.nav-bar{position:absolute;left:0;top:36px;width:710px;height:70px;background:var(--nav-bg);display:flex;justify-content:space-around;align-items:center;padding:0 40px}
.nav-bar svg{width:34px;height:34px}
.level-tabs{position:absolute;top:120px;left:0;width:710px;display:flex;justify-content:center;gap:16px}
.level-tab{width:106px;height:24px;border-radius:12px;background:var(--pill-grey);color:var(--white);font-size:11px;text-transform:uppercase;display:flex;align-items:center;justify-content:center}
.level-tab.is-active{background:var(--pink)}
.level-picker{position:absolute;top:166px;left:0;width:710px;display:flex;align-items:center;justify-content:space-between;padding:0 18px}
.level-picker .arrow{width:18px;height:26px}
.level-badge{width:68px;height:68px;border-radius:50%;background:var(--white);box-shadow:0 1px 3px rgba(0,0,0,.12);display:flex;align-items:center;justify-content:center}
.level-badge span{width:60px;height:60px;border-radius:50%;background:var(--navy);color:var(--white);display:flex;flex-direction:column;align-items:center;justify-content:center;font-weight:600;font-size:24px;line-height:1}
.level-badge.is-recent span{background:var(--pink)}
.level-badge small{font-size:9px;font-weight:400;margin-top:3px}
.search{position:absolute;top:258px;left:22px;width:666px;height:46px;border-radius:8px;background:var(--white);display:flex;align-items:center;justify-content:center;color:var(--text-light);font-size:18px}
.search svg{position:absolute;right:16px;top:11px;width:26px;height:26px}
.opponents{position:absolute;left:0;width:710px;display:flex;justify-content:space-around;padding:0 28px}
.row-one{top:340px}
.row-two{top:628px}
.divider{position:absolute;top:590px;left:22px;width:666px;height:1px;background:var(--line)}
.opponent{width:170px;display:flex;flex-direction:column;align-items:center}
.avatar{width:166px;height:166px;border-radius:50%;border:4px solid var(--white);box-shadow:0 1px 4px rgba(0,0,0,.15)}
.avatar.tone-a{background:linear-gradient(160deg,#c9b8a6,#6a4b3a)}
.avatar.tone-b{background:linear-gradient(160deg,#9aa0a6,#4d3b33)}
.avatar.tone-c{background:linear-gradient(160deg,#d8cfc8,#3a2f2f)}
.opponent-name{margin-top:-20px;width:136px;height:30px;border-radius:15px;background:var(--white);font-size:16px;color:var(--text-mid);display:flex;align-items:center;justify-content:center;position:relative}
.opponent-actions{margin-top:8px;display:flex;gap:12px}
.opponent-actions svg{width:28px;height:28px}
.cards{position:absolute;top:868px;left:12px;width:686px;display:flex;gap:14px}
.card{flex:1;height:228px;background:var(--white);border:1px solid #e2e2e2;position:relative}
.card .close{position:absolute;top:10px;right:10px;width:22px;height:22px;background:#b3b3b3;color:var(--white);font-size:13px;font-weight:700;display:flex;align-items:center;justify-content:center}
.message-avatar{position:absolute;left:20px;top:28px;width:66px;height:72px;border-radius:40%;background:linear-gradient(160deg,#f0c7a6,#b9774f)}
.message-body{position:absolute;left:108px;top:14px;width:200px}
.message-label{font-size:12px;color:var(--pink)}
.message-from{font-size:20px;font-weight:600;margin-top:4px}
.message-text{font-size:13px;line-height:18px;color:var(--text-light);margin-top:14px}
.message-footer{position:absolute;right:14px;bottom:14px;display:flex;align-items:center;gap:10px;font-size:11px;color:var(--text-mid)}
.game-art{position:absolute;left:6px;top:6px;right:6px;height:146px;background:linear-gradient(180deg,#6cc4e8,#9ed27a 70%,#5e9f3d)}
.invite-text{position:absolute;left:20px;top:158px;width:200px;font-size:13px;line-height:17px;color:var(--text-light)}
.invite-text em{font-style:normal;color:var(--pink)}
.invite-actions{position:absolute;right:14px;top:170px;display:flex;gap:12px}
.invite-actions span{width:26px;height:26px;border-radius:50%;display:flex;align-items:center;justify-content:center}
.accept{background:var(--ok)}
.decline{background:var(--pink)}
.play-random{position:absolute;top:1110px;left:50px;width:610px;height:72px;background:var(--pink);color:var(--white);font-size:30px;font-weight:600;display:flex;align-items:center;justify-content:center}
</style>
</head>
<body>
<header class="status-bar">
  <div class="carrier">
    <svg width="40" height="18" viewBox="0 0 40 18"><rect x="0" y="12" width="5" height="6" fill="#fff"/><rect x="8" y="9" width="5" height="9" fill="#fff"/><rect x="16" y="6" width="5" height="12" fill="#fff"/><rect x="24" y="3" width="5" height="15" fill="#fff"/><rect x="32" y="0" width="5" height="18" fill="#fff"/></svg>
    <span>DINE</span>
  </div>
  <div class="time">10:35 AM</div>
  <div class="battery">
    <svg width="20" height="20" viewBox="0 0 20 20"><circle cx="10" cy="10" r="9" fill="#fff"/><path d="M10 4v6h4" stroke="#2a2a31" stroke-width="2" fill="none"/></svg>
    <span>65%</span>
    <svg width="42" height="20" viewBox="0 0 42 20"><rect x="1" y="1" width="36" height="18" rx="3" fill="none" stroke="#fff" stroke-width="2"/><rect x="4" y="4" width="22" height="12" fill="#fff"/><rect x="38" y="6" width="3" height="8" fill="#fff"/></svg>
  </div>
</header>

<nav class="nav-bar">
  <svg viewBox="0 0 34 34" aria-label="Settings"><circle cx="17" cy="17" r="9" fill="none" stroke="var(--nav-icon)" stroke-width="5" stroke-dasharray="4 3"/><circle cx="17" cy="17" r="7" fill="none" stroke="var(--nav-icon)" stroke-width="3"/></svg>
  <svg viewBox="0 0 34 34" aria-label="Shop"><path d="M3 7h5l4 16h16l3-12H10" fill="none" stroke="var(--nav-icon)" stroke-width="2.5"/><circle cx="14" cy="28" r="2.5" fill="var(--nav-icon)"/><circle cx="26" cy="28" r="2.5" fill="var(--nav-icon)"/><path d="M20 12v5M20 19v1.5" stroke="var(--nav-icon)" stroke-width="2.5"/></svg>
  <svg viewBox="0 0 34 34" aria-label="Leaderboards"><path d="M8 3h13l6 6v22H8z" fill="none" stroke="var(--nav-icon)" stroke-width="2.5"/><path d="M12 15h11M12 20h11M12 25h11" stroke="var(--nav-icon)" stroke-width="2"/></svg>
  <svg viewBox="0 0 34 34" aria-label="Achievements"><circle cx="17" cy="15" r="6" fill="var(--nav-icon)"/><rect x="14" y="22" width="6" height="5" fill="var(--nav-icon)"/><path d="M17 2v4M6 6l3 3M28 6l-3 3M3 15h4M27 15h4" stroke="var(--nav-icon)" stroke-width="2"/></svg>
</nav>

<div class="level-tabs">
  <span class="level-tab">Recent levels</span>
  <span class="level-tab is-active">Choose level</span>
  <span class="level-tab">Random</span>
</div>

<div class="level-picker">
  <svg class="arrow" viewBox="0 0 18 26"><path d="M13 3L4 13l9 10" fill="none" stroke="var(--navy)" stroke-width="2"/></svg>
  <div class="level-badge is-recent"><span>15<small>level</small></span></div>
  <div class="level-badge is-recent"><span>4<small>level</small></span></div>
  <div class="level-badge"><span>32<small>level</small></span></div>
  <div class="level-badge"><span>71<small>level</small></span></div>
  <div class="level-badge"><span>18<small>level</small></span></div>
  <div class="level-badge"><span>69<small>level</small></span></div>
  <svg class="arrow" viewBox="0 0 18 26"><path d="M5 3l9 10-9 10" fill="none" stroke="var(--navy)" stroke-width="2"/></svg>
</div>

<div class="search">search opponent
  <svg viewBox="0 0 26 26"><circle cx="11" cy="11" r="8" fill="none" stroke="#c4c4c4" stroke-width="2"/><path d="M17 17l7 7" stroke="#c4c4c4" stroke-width="2"/></svg>
</div>

<section class="opponents row-one">
  <div class="opponent"><div class="avatar tone-a" role="img" aria-label="Opponent photo of Maren Holt"></div><div class="opponent-name">Maren Holt</div>
    <div class="opponent-actions">
      <svg viewBox="0 0 28 28"><path d="M14 3l3.3 7 7.7.9-5.7 5.2 1.5 7.6L14 20l-6.8 3.7 1.5-7.6L3 10.9l7.7-.9z" fill="var(--icon-grey)"/></svg>
      <svg viewBox="0 0 28 28"><path d="M14 24L4 14a5.5 5.5 0 0110-7 5.5 5.5 0 0110 7z" fill="var(--icon-grey)"/></svg>
      <svg viewBox="0 0 28 28"><path d="M3 5h22v14H12l-6 5v-5H3z" fill="var(--icon-grey)"/></svg>
    </div></div>
  <div class="opponent"><div class="avatar tone-b" role="img" aria-label="Opponent photo of Theo V"></div><div class="opponent-name">Theo V</div>
    <div class="opponent-actions">
      <svg viewBox="0 0 28 28"><path d="M14 3l3.3 7 7.7.9-5.7 5.2 1.5 7.6L14 20l-6.8 3.7 1.5-7.6L3 10.9l7.7-.9z" fill="var(--icon-grey)"/></svg>
      <svg viewBox="0 0 28 28"><path d="M14 24L4 14a5.5 5.5 0 0110-7 5.5 5.5 0 0110 7z" fill="var(--icon-grey)"/></svg>
      <svg viewBox="0 0 28 28"><path d="M3 5h22v14H12l-6 5v-5H3z" fill="var(--icon-grey)"/></svg>
    </div></div>
  <div class="opponent"><div class="avatar tone-c" role="img" aria-label="Opponent photo of Nina K"></div><div class="opponent-name">Nina K</div>
    <div class="opponent-actions">
      <svg viewBox="0 0 28 28"><path d="M14 3l3.3 7 7.7.9-5.7 5.2 1.5 7.6L14 20l-6.8 3.7 1.5-7.6L3 10.9l7.7-.9z" fill="var(--icon-grey)"/></svg>
      <svg viewBox="0 0 28 28"><path d="M14 24L4 14a5.5 5.5 0 0110-7 5.5 5.5 0 0110 7z" fill="var(--icon-grey)"/></svg>
      <svg viewBox="0 0 28 28"><path d="M3 5h22v14H12l-6 5v-5H3z" fill="var(--icon-grey)"/></svg>
    </div></div>
</section>

<div class="divider"></div>

<section class="opponents row-two">
  <div class="opponent"><div class="avatar tone-a" role="img" aria-label="Opponent photo of Maren Holt"></div><div class="opponent-name">Maren Holt</div>
    <div class="opponent-actions">
      <svg viewBox="0 0 28 28"><path d="M14 3l3.3 7 7.7.9-5.7 5.2 1.5 7.6L14 20l-6.8 3.7 1.5-7.6L3 10.9l7.7-.9z" fill="var(--icon-grey)"/></svg>
      <svg viewBox="0 0 28 28"><path d="M14 24L4 14a5.5 5.5 0 0110-7 5.5 5.5 0 0110 7z" fill="var(--icon-grey)"/></svg>
      <svg viewBox="0 0 28 28"><path d="M3 5h22v14H12l-6 5v-5H3z" fill="var(--icon-grey)"/></svg>
    </div></div>
  <div class="opponent"><div class="avatar tone-b" role="img" aria-label="Opponent photo of Theo V"></div><div class="opponent-name">Theo V</div>
    <div class="opponent-actions">
      <svg viewBox="0 0 28 28"><path d="M14 3l3.3 7 7.7.9-5.7 5.2 1.5 7.6L14 20l-6.8 3.7 1.5-7.6L3 10.9l7.7-.9z" fill="var(--icon-grey)"/></svg>
      <svg viewBox="0 0 28 28"><path d="M14 24L4 14a5.5 5.5 0 0110-7 5.5 5.5 0 0110 7z" fill="var(--icon-grey)"/></svg>
      <svg viewBox="0 0 28 28"><path d="M3 5h22v14H12l-6 5v-5H3z" fill="var(--icon-grey)"/></svg>
    </div></div>
  <div class="opponent"><div class="avatar tone-c" role="img" aria-label="Opponent photo of Nina K"></div><div class="opponent-name">Nina K</div>
    <div class="opponent-actions">
      <svg viewBox="0 0 28 28"><path d="M14 3l3.3 7 7.7.9-5.7 5.2 1.5 7.6L14 20l-6.8 3.7 1.5-7.6L3 10.9l7.7-.9z" fill="var(--icon-grey)"/></svg>
      <svg viewBox="0 0 28 28"><path d="M14 24L4 14a5.5 5.5 0 0110-7 5.5 5.5 0 0110 7z" fill="var(--icon-grey)"/></svg>
      <svg viewBox="0 0 28 28"><path d="M3 5h22v14H12l-6 5v-5H3z" fill="var(--icon-grey)"/></svg>
    </div></div>
</section>

<section class="cards">
  <article class="card message-card">
    <span class="close">×</span>
    <div class="message-avatar" role="img" aria-label="Sender photo of Owen Marsh"></div>
    <div class="message-body">
      <p class="message-label">message from</p>
      <p class="message-from">Owen Marsh</p>
      <p class="message-text">Ex timeam nostrum his, usu eius oportere ex, quod vero nostro at duo. Nam cu mutat eloquentiam, sea et posse ornatus, eam latine labores</p>
    </div>
    <div class="message-footer">read all messages
      <svg width="26" height="18" viewBox="0 0 26 18"><rect width="26" height="18" fill="var(--pink)"/><path d="M1 1l12 9 12-9" fill="none" stroke="#fff" stroke-width="1.5"/></svg>
    </div>
  </article>
  <article class="card invite-card">
    <div class="game-art" role="img" aria-label="Game artwork for Tower Realm Outposts"></div>
    <span class="close">×</span>
    <p class="invite-text">Your friend <em>Clara B</em> just played a game. Wanna try it too?</p>
    <div class="invite-actions">
      <span class="accept"><svg width="14" height="14" viewBox="0 0 14 14"><path d="M2 7l3 3 7-7" fill="none" stroke="#fff" stroke-width="2.2"/></svg></span>
      <span class="decline"><svg width="12" height="12" viewBox="0 0 12 12"><path d="M2 2l8 8M10 2l-8 8" stroke="#fff" stroke-width="2.2"/></svg></span>
    </div>
  </article>
</section>

<div class="play-random">Play a random game</div>
</body>
</html>
```